Hedwig Sommerau - Entwicklung für Menschen und Organisationen
Kreative Ideen, die sehr professionell umgesetzt werden und selbstständig verbesserte Versionen werden zur Verfügung gestellt. DANKE!
Zielgruppe
Ich biete Organisationsentwicklungen, Coachings, Teamentwicklungen, Moderationen, Führungskräfteentwicklung, Konfliktklärung und Seminare an.
Meine Zielgruppe sind Vorstände, Geschäftsführer, Personaler, Führungskräfte und andere 'Entscheider'.
Aufgabenstellung
Das Format soll in ein DIN lang Kuvert passen, jedoch gerne nicht das klassische zweifach-gefaltete A4 sein.
Es soll zu meinem Logo und den Druckstücken passen.
Es soll herauskommen, dass alle Leistungen in der Organisationsentwicklung enthalten sein können, diese jedoch auch jeweils einzeln angeboten werden können.
Ich benötige die Broschüre als "offene" Datei, da ich in naher Zukunft die Geschäftsräume wechsele.

```html
<!DOCTYPE html>
<html lang="de">
<head>
<meta charset="utf-8">
<title>Hedwig Sommerau – Faltblatt Innenseite</title>
<link href="https://fonts.googleapis.com/css2?family=Open+Sans:wght@400;600;700&display=swap" rel="stylesheet">
<style>
  :root {
    --brand-red: #e3222b;
    --earth-brown: #5a5046;
    --ink: #1c1c1c;
    --paper: #ffffff;
    --fold-line: #3a3a3a;
    --photo-tone-a: #c9c6c4;
    --photo-tone-b: #6b625b;
  }
  * { margin: 0; padding: 0; box-sizing: border-box; }
  html, body { width: 1200px; height: 796px; overflow: hidden; background: var(--paper); }
  body { font-family: "Open Sans", Arial, sans-serif; color: var(--ink); }

  .spread { position: relative; width: 1200px; height: 796px; overflow: hidden; }

  .fold { position: absolute; top: 0; width: 1px; height: 796px; background: var(--fold-line); }
  .fold--left { left: 398px; }

  /* Benefits panel */
  .benefits__title {
    position: absolute; left: 40px; top: 68px;
    font-size: 28px; font-weight: 600; letter-spacing: 1.8px; line-height: 35px;
    text-transform: uppercase;
  }
  .benefit { position: absolute; left: 38px; width: 318px; }
  .benefit__marker {
    position: absolute; left: 0; top: 0; width: 36px; height: 36px;
    background: var(--brand-red); border-radius: 3px;
  }
  .benefit__heading {
    margin-left: 51px; font-size: 13.6px; font-weight: 700; line-height: 18px;
  }
  .benefit__text {
    margin-left: 51px; margin-top: 6px; width: 267px;
    font-size: 13.3px; line-height: 17.5px; text-align: justify; hyphens: manual;
  }
  .benefit--one { top: 192px; }
  .benefit--two { top: 323px; }
  .benefit--three { top: 508px; }

  /* Contact panel */
  .contact-band { position: absolute; left: 0; top: 0; }
  .contact {
    position: absolute; left: 537px; top: 262px; color: var(--paper);
  }
  .contact__title { font-size: 27.5px; font-weight: 400; letter-spacing: 2px; line-height: 34px; margin-left: -4px; }
  .contact__name { margin-top: 50px; font-size: 13.5px; font-weight: 700; }
  .contact__lines { font-size: 13.5px; line-height: 20.5px; }
  .contact__address { margin-top: 8px; }
  .contact__phones { margin-top: 13px; }
  .contact__web { margin-top: 20px; }
  .contact__label { display: inline-block; width: 24px; }

  /* Cover panel */
  .brand { position: absolute; left: 843px; top: 158px; width: 314px; }
  .brand__name {
    display: flex; align-items: center; gap: 9px;
    font-size: 31px; font-weight: 700; color: var(--earth-brown); line-height: 40px; white-space: nowrap;
  }
  .brand__dot { width: 14px; height: 14px; border-radius: 50%; background: var(--brand-red); flex: none; }
  .brand__tagline {
    margin-top: 4px; font-size: 13.7px; font-weight: 600; color: var(--earth-brown);
    letter-spacing: -0.2px; white-space: nowrap;
  }
  .portrait {
    position: absolute; left: 843px; top: 305px; width: 313px; height: 418px;
    border-radius: 4px;
    background: linear-gradient(160deg, var(--photo-tone-a) 0%, #b9ada2 45%, var(--photo-tone-b) 100%);
  }
</style>
</head>
<body>
<main class="spread">

  <section class="benefits">
    <h1 class="benefits__title">Ihre Vorteile durch<br>meine Begleitung</h1>

    <article class="benefit benefit--one">
      <span class="benefit__marker"></span>
      <h2 class="benefit__heading">Individuell, ganz nach Ihren Bedarf</h2>
      <p class="benefit__text">Menschen und Unternehmen sind einzig­artig. In diesem Bewusstsein konzipiere ich jeden Prozess ganz individuell nach Ihrer aktuellen Situation.</p>
    </article>

    <article class="benefit benefit--two">
      <span class="benefit__marker"></span>
      <h2 class="benefit__heading">Die Menschen stets im Fokus</h2>
      <p class="benefit__text">Erfolgreich können Unternehmen nur werden und sein, wenn deren Mitarbeiter motiviert und engagiert sind. Um dies zu erreichen, müssen sie beteiligt und informiert sein. Ich sorge durch die konsequente Einbindung Ihrer Mitarbeiter für nachhaltigen Erfolg Ihrer Prozesse.</p>
    </article>

    <article class="benefit benefit--three">
      <span class="benefit__marker"></span>
      <h2 class="benefit__heading">Ihre Ressourcen führen zum Erfolg</h2>
      <p class="benefit__text">Meine Arbeiten zielt darauf ab, mit geeig­neten Modellen, Methoden und Prozessen, die Ressourcen und Fähigkeiten von Ihren Mitarbeitern und Ihnen zu nutzen, um mit Ihnen die beste und authentischste Lösung für Ihr Unternehmen zu entwickeln.</p>
    </article>
  </section>

  <div class="fold fold--left"></div>

  <svg class="contact-band" width="1200" height="796" viewBox="0 0 1200 796" aria-hidden="true">
    <path d="M605,0 Q348,458 580,796 L800,796 L800,0 Z" fill="var(--earth-brown)"/>
    <line x1="800.5" y1="0" x2="800.5" y2="796" stroke="var(--fold-line)" stroke-width="1"/>
  </svg>

  <section class="contact">
    <h2 class="contact__title">KONTAKTDATEN</h2>
    <p class="contact__name">Hedwig Sommerau</p>
    <div class="contact__lines contact__address">
      <div>Birkenweg 14</div>
      <div>91522 Lindenstadt</div>
    </div>
    <div class="contact__lines contact__phones">
      <div><span class="contact__label">T</span>0913 / 4482 3061</div>
      <div><span class="contact__label">H</span>0171 / 58 27 469</div>
      <div><span class="contact__label">F</span>0913/ 4482 3062</div>
    </div>
    <div class="contact__lines contact__web">
      <div><span class="contact__label">M</span>anfrage@hedwig-sommerau.de</div>
      <div><span class="contact__label">W</span>www.hedwig-sommerau.de</div>
    </div>
  </section>

  <section class="cover">
    <div class="brand">
      <div class="brand__name"><span class="brand__dot"></span>Hedwig Sommerau</div>
      <div class="brand__tagline">Entwicklung für Menschen und Organisationen</div>
    </div>
    <div class="portrait" role="img" aria-label="Porträtfoto von Hedwig Sommerau im dunklen Blazer vor hellgrauem Hintergrund"></div>
  </section>

</main>
</body>
</html>
```